New Innovative Counselling and psychotherapy Service needs Business Card design

Keep it simple and professional. On one side, just company name and logo (perhaps in all blue) and maybe a tag line.

On other side (all white) my name and Qualifications in centre

Industry/Entity Type

Health And Wellness

Contact Information for Business Card

Dara Whelby
Counsellor & Psychotherapist
BSc (Psychol.), BA, Dip. (Couns. & Psych.), PG.Cert (CBT), FGTrK, ONRE

I will also require Mobile no, Email and web site address of which I'll pass on to final designer.

Font styles to use
Sans Serif

Requirements
Must have
• My Logo Only and please use the colours in logo that is in it.
Should not have
• Any other images

```html
<!DOCTYPE html>
<html lang="en">
<head>
<meta charset="utf-8">
<title>Harbor Path – Business Card</title>
<link rel="stylesheet" href="https://fonts.googleapis.com/css2?family=Open+Sans:wght@300;400;600;700&display=swap">
<style>
  :root {
    --sky: #3fb3ec;
    --sky-deep: #2fa4e0;
    --paper: #ffffff;
    --stage: #e9ecef;
    --ink: #4a4f55;
    --ink-soft: #6b7076;
    --halo: #eef3f8;
  }
  * { margin: 0; padding: 0; box-sizing: border-box; }
  html, body {
    width: 1200px; height: 900px; overflow: hidden;
    background: var(--stage);
    font-family: "Open Sans", sans-serif;
  }
  .stage {
    width: 1200px; height: 900px;
    display: flex; flex-direction: column; align-items: center; justify-content: center;
    gap: 40px;
  }
  .card {
    width: 700px; height: 400px;
    position: relative; overflow: hidden;
    box-shadow: 0 10px 30px rgba(0,0,0,.18);
  }

  /* Front: white side */
  .card-front { background: var(--paper); }
  .front-brand {
    position: absolute; left: 0; right: 0; top: 135px;
    display: flex; align-items: center; justify-content: center; gap: 16px;
  }
  .brand-dot {
    width: 34px; height: 34px; border-radius: 50%; background: var(--sky);
  }
  .front-brand .brand-name {
    font-size: 46px; font-weight: 400; color: var(--sky); letter-spacing: .5px;
  }
  .tagline {
    position: absolute; left: 0; right: 0; bottom: 52px;
    text-align: center; font-size: 15px; color: var(--ink-soft); letter-spacing: .3px;
  }

  /* Back: blue side */
  .card-back { background: var(--sky); color: var(--paper); }
  .halo {
    position: absolute; left: 330px; top: -70px;
    width: 440px; height: 440px; border-radius: 50%;
    background: var(--halo); opacity: .93;
  }
  .back-brand {
    position: absolute; left: 390px; top: 125px;
    display: flex; align-items: center; gap: 12px;
  }
  .back-brand .brand-dot { width: 26px; height: 26px; }
  .back-brand .brand-name {
    font-size: 30px; font-weight: 400; color: var(--ink);
  }
  .person {
    position: absolute; left: 40px; top: 150px;
  }
  .person-name {
    font-size: 22px; font-weight: 700; letter-spacing: .5px; text-transform: uppercase;
  }
  .person-role {
    font-size: 16px; font-weight: 400; text-transform: uppercase; margin-top: 4px; letter-spacing: .3px;
  }
  .person-quals {
    font-size: 12px; line-height: 1.45; margin-top: 4px;
  }
  .contacts {
    position: absolute; left: 40px; bottom: 40px;
    list-style: none; font-size: 15px; line-height: 1;
  }
  .contacts li { display: flex; align-items: center; gap: 12px; margin-top: 9px; }
  .contacts svg { width: 16px; height: 16px; flex: none; }
</style>
</head>
<body>
<main class="stage">
  <section class="card card-front">
    <div class="front-brand">
      <span class="brand-dot"></span>
      <span class="brand-name">Harbor Path</span>
    </div>
    <p class="tagline">Caring For Your Psychological Well-Being Is Our Top Priority</p>
  </section>

  <section class="card card-back">
    <div class="halo"></div>
    <div class="back-brand">
      <span class="brand-dot"></span>
      <span class="brand-name">Harbor Path</span>
    </div>

    <div class="person">
      <h1 class="person-name">Dara Whelby</h1>
      <p class="person-role">Counsellor &amp; Psychotherapist</p>
      <p class="person-quals">BSc (Psychol.), BA, Dip. (Couns. &amp; Psych.)<br>PG.Cert (CBT), FGTrK,</p>
    </div>

    <ul class="contacts">
      <li>
        <svg viewBox="0 0 16 16" aria-hidden="true"><rect x="4" y="1" width="8" height="14" rx="1.5" fill="none" stroke="#fff" stroke-width="1.6"/><circle cx="8" cy="12.2" r=".9" fill="#fff"/></svg>
        <span>555 201 7730</span>
      </li>
      <li>
        <svg viewBox="0 0 16 16" aria-hidden="true"><rect x="1" y="3" width="14" height="10" rx="1" fill="#fff"/><path d="M1.5 3.5 8 9l6.5-5.5" fill="none" stroke="#3fb3ec" stroke-width="1.4"/></svg>
        <span>dara@Harborpath.com</span>
      </li>
      <li>
        <svg viewBox="0 0 16 16" aria-hidden="true"><circle cx="8" cy="8" r="6.5" fill="none" stroke="#fff" stroke-width="1.5"/><ellipse cx="8" cy="8" rx="2.8" ry="6.5" fill="none" stroke="#fff" stroke-width="1.2"/><path d="M1.5 8h13" stroke="#fff" stroke-width="1.2"/></svg>
        <span>www.Harborpath.com</span>
      </li>
    </ul>
  </section>
</main>
</body>
</html>
```